Business Card Design Project

I require a business card with the following information on them for various different people;
name
m:
f:
e:
I have a logo already and will attached that. We are in the construction industry. I require something clean and simple but eye catching at the same time. You can use another colour with our logo if you like and you can style the logo as well if you wish. I am open.
Also it needs to be front and back design.
Industry/Entity Type
Construction
Requirements
Must have
- Logo, name, mobile, fax and email address.
Front and back design

```html
<!DOCTYPE html>
<html lang="en">
<head>
<meta charset="utf-8">
<title>Ridgeway Developments – Business Card</title>
<link rel="stylesheet" href="https://fonts.googleapis.com/css2?family=PT+Sans:wght@400;700&display=swap">
<style>
  :root {
    --backdrop: #e7e3de;
    --card: #ffffff;
    --brand-green: #4f9a3a;
    --lime: #c9df5f;
    --mid-green: #6fa83a;
    --forest: #3e7a2b;
    --ink: #4a4a4a;
  }
  * { box-sizing: border-box; margin: 0; padding: 0; }
  html, body { width: 1200px; height: 407px; overflow: hidden; }
  body {
    background: var(--backdrop);
    font-family: "PT Sans", Arial, sans-serif;
    color: var(--ink);
    position: relative;
  }
  .card {
    position: absolute;
    top: 60px;
    width: 504px;
    height: 288px;
    background: var(--card);
    box-shadow: 0 3px 8px rgba(0,0,0,0.35);
    overflow: hidden;
  }
  .card--front { left: 58px; }
  .card--back { left: 640px; }
  .card__band {
    position: absolute;
    left: 0; right: 0; bottom: 0;
    height: 32px;
    background: linear-gradient(90deg, var(--lime) 0%, var(--mid-green) 50%, var(--forest) 100%);
  }
  .brand {
    position: absolute;
    left: 0; right: 0;
    display: flex;
    align-items: center;
    justify-content: center;
    gap: 10px;
    color: var(--brand-green);
    font-weight: 400;
    white-space: nowrap;
  }
  .brand__mark { background: var(--brand-green); display: block; }
  .card--front .brand { top: 58px; font-size: 34px; }
  .card--front .brand__mark { width: 30px; height: 30px; }
  .card--back .brand { top: 122px; font-size: 30px; }
  .card--back .brand__mark { width: 26px; height: 26px; }
  .holder {
    position: absolute;
    top: 176px; left: 0; right: 0;
    text-align: center;
    font-size: 16px;
  }
  .holder__name { font-weight: 700; }
  .holder__title { font-size: 13px; }
  .contact {
    position: absolute;
    top: 218px; left: 0; right: 0;
    text-align: center;
    font-size: 13px;
    line-height: 22px;
  }
</style>
</head>
<body>
  <section class="card card--front" aria-label="Card front">
    <div class="brand"><span class="brand__mark"></span>Ridgeway Developments</div>
    <p class="holder"><span class="holder__name">Your Name</span> <span class="holder__title">/ Title</span></p>
    <p class="contact">C : 123-456-7890&nbsp;&nbsp;F : 123-456-7890<br>E : name@website.com</p>
    <div class="card__band" role="img" aria-label="Decorative green swoosh band"></div>
  </section>

  <section class="card card--back" aria-label="Card back">
    <div class="brand"><span class="brand__mark"></span>Ridgeway Developments</div>
    <div class="card__band" role="img" aria-label="Decorative green swoosh band"></div>
  </section>
</body>
</html>
```